NZ First of it's kind solutions directory and marketplace for busy Mums needs a business card design

We need a business card design for our new nationwide business in NZ (long term plans to go global). We provide solutions to the everyday challenges that busy Mums face by connecting them with quality communities and suppliers of carefully selected, relevant products and services. We sell direct via our online marketplace. The final design should communicate our values of inclusivity, quality and smart solutions. Colours should incorporate our logo colour palette of #477077 and #6ba8b2. Our website is at https://www.brightnestmums.example

Target Market(s)

busy Mums, Age 28 – 50, female, income over $100K, location main centres NZ primarily but NZ wide. Is likely juggling work or career with a young family. Probably had hobbies which have fallen by the wayside.
-Wants to succeed in her chosen career without compromising on family life
-to successfully juggle her career without feeling like she is compromising her children
- Is time poor, something always has to give and it’s generally her health (she’ll stay up late, get stressed)
- probably ex corporate or professional career. Has discretional income

Industry/Entity Type

Business

Contact Information for Business Card

Lena Forbisher, Founder, BrightNestMums.example (Strapline Tap; Gather; Sorted), 47 Kowhai Terrace, Ellerslie, Auckland 1051, New Zealand. Mob: 021 483 517 Ph: +64 (0)9 571 4860

Font styles to use
Other font styles liked:
• Raleway, and/or Architects Daughter

Colors
00a990
33b8a4
86cfc6
cfeae6

Requirements
Must have
• the above details, streamline. the logo and colours associated with those logos
Should not have
• foil or metallic colours

```html
<!DOCTYPE html>
<html lang="en">
<head>
<meta charset="utf-8">
<title>BrightNestMums — Business Card</title>
<link rel="stylesheet" href="https://fonts.googleapis.com/css2?family=Work+Sans:wght@400;500;600&display=swap">
<style>
  :root {
    --teal-deep: #477077;
    --teal-light: #6ba8b2;
    --paper: #ffffff;
    --backdrop: #262626;
    --ink: #477077;
  }
  * { box-sizing: border-box; margin: 0; padding: 0; }
  html, body {
    width: 1200px;
    height: 900px;
    overflow: hidden;
    background: var(--backdrop);
    font-family: "Work Sans", Arial, sans-serif;
  }
  .stage {
    width: 1200px;
    height: 900px;
    display: flex;
    flex-direction: column;
    align-items: center;
    justify-content: center;
    gap: 44px;
  }
  .card {
    width: 660px;
    height: 377px;
    position: relative;
    box-shadow: 0 8px 24px rgba(0,0,0,0.45);
  }
  .card--front { background: var(--teal-deep); }
  .card--back { background: var(--paper); }

  .brand {
    display: flex;
    align-items: center;
    gap: 14px;
  }
  .brand__dot {
    width: 34px;
    height: 34px;
    border-radius: 50%;
    flex: none;
  }
  .brand__name {
    font-weight: 600;
    letter-spacing: -0.5px;
    white-space: nowrap;
  }

  .card--front .brand {
    position: absolute;
    left: 0; right: 0; top: 128px;
    justify-content: center;
  }
  .card--front .brand__dot { background: var(--paper); width: 44px; height: 44px; }
  .card--front .brand__name { color: var(--paper); font-size: 46px; }
  .front__web {
    position: absolute;
    left: 0; right: 0; bottom: 52px;
    text-align: center;
    color: var(--paper);
    font-size: 15px;
    letter-spacing: 1px;
  }

  .card--back .brand {
    position: absolute;
    left: 40px;
    top: 166px;
  }
  .card--back .brand__dot { background: var(--teal-deep); width: 30px; height: 30px; }
  .card--back .brand__name { color: var(--teal-deep); font-size: 27px; }

  .back__divider {
    position: absolute;
    left: 318px;
    top: 104px;
    width: 2px;
    height: 170px;
    background: var(--teal-deep);
  }
  .contact {
    position: absolute;
    left: 342px;
    top: 102px;
    color: var(--ink);
  }
  .contact__name {
    font-size: 30px;
    font-weight: 500;
    line-height: 1;
    letter-spacing: 0.5px;
  }
  .contact__role {
    font-size: 15px;
    letter-spacing: 1px;
    margin-top: 4px;
  }
  .contact__address {
    font-size: 15px;
    letter-spacing: 1px;
    line-height: 1.3;
    margin-top: 14px;
    font-style: normal;
  }
  .contact__lines {
    list-style: none;
    margin-top: 8px;
    font-size: 15px;
    letter-spacing: 1px;
    line-height: 1.35;
  }
  .contact__lines li {
    display: flex;
    align-items: center;
    gap: 7px;
  }
  .contact__icon { width: 11px; height: 11px; flex: none; }
</style>
</head>
<body>
  <main class="stage">
    <section class="card card--front" aria-label="Card front">
      <div class="brand">
        <span class="brand__dot"></span>
        <span class="brand__name">BrightNestMums</span>
      </div>
      <p class="front__web">www.brightnestmums.example</p>
    </section>

    <section class="card card--back" aria-label="Card back">
      <div class="brand">
        <span class="brand__dot"></span>
        <span class="brand__name">BrightNestMums</span>
      </div>
      <div class="back__divider"></div>
      <div class="contact">
        <h1 class="contact__name">Lena Forbisher</h1>
        <p class="contact__role">Founder</p>
        <address class="contact__address">47 Kowhai Terrace, Ellerslie<br>Auckland 1051, New Zealand</address>
        <ul class="contact__lines">
          <li>
            <svg class="contact__icon" viewBox="0 0 12 12" aria-hidden="true"><rect x="3" y="0.8" width="6" height="10.4" rx="1.2" fill="none" stroke="#477077" stroke-width="1.4"/><rect x="5" y="9" width="2" height="1" fill="#477077"/></svg>
            021 483 517
          </li>
          <li>
            <svg class="contact__icon" viewBox="0 0 12 12" aria-hidden="true"><path d="M2.5 1 L4.6 1 L5.3 3.6 L4 4.6 Q5 7 7.4 8 L8.4 6.7 L11 7.4 L11 9.5 Q10.5 11 9 11 Q1 10 1 2.6 Q1 1 2.5 1 Z" fill="#477077"/></svg>
            +64 (0)9 571 4860
          </li>
          <li>
            <svg class="contact__icon" viewBox="0 0 12 12" aria-hidden="true"><g fill="none" stroke="#477077" stroke-width="1"><circle cx="6" cy="6" r="5"/><ellipse cx="6" cy="6" rx="2.2" ry="5"/><line x1="1" y1="6" x2="11" y2="6"/><line x1="2" y1="3.4" x2="10" y2="3.4"/><line x1="2" y1="8.6" x2="10" y2="8.6"/></g></svg>
            www.brightnestmums.example
          </li>
        </ul>
      </div>
    </section>
  </main>
</body>
</html>
```